Website Comps for Famous Southern BBQ Restaurant in Alabama

We need an authentic, brand-focused redesign for a restaurant.

We need an authentic look.
The client really likes this website.
https://pelmarsmokehouse.example/

I don't want to see a bunch of crazy colors.
Avoid image sliders on the homepage. I hate those.

Please mockup the following three pages:
Homepage
Interior page (for mockup purposes, you can do an About page)
Menu page

I only need the PSD's; not the website coded.

Here is the current website: www.kortiespit.example

https://pelmarsmokehouse.example/

Here are some additional stock photos. New photos will be shot, but these may help for your mock-up designs.
https://files.quillbox.example/sh/83kkqvtrd41zpa7/XQM20PbT9LyRk-wnEuvJ3tpd?dl=0
Updates

I realize we don't have a lot of high-quality photos to work with.Those will be shot.Here are some additional stock photos that may help.https://files.quillbox.example/sh/83kkqvtrd41zpa7/XQM20PbT9LyRk-wnEuvJ3tpd?dl=0 Added Saturday, June 10, 2017

Target Market(s)

United states

Industry/Entity Type

Restaurant

Number of Pages Required

3 page

Font styles to use
Sans Serif

Colors

Designer to choose colors to be used in the design.

Requirements
Must have
• An authentic look.
• The client really likes this website.
• https://pelmarsmokehouse.example/
• It's simple, bold, and vintage at the same time.
• That is what we want.
• Our existing website is
• kortiespit.example
Nice to have
• Simplicity. Something that makes the food look good.
• Possibly a background.
• Logo:
• https://files.quillbox.example/s/t62bnezwhk0qpl3/kories-pit-lakeview.png?dl=0
• Here is a sampling of photos for your comps:
• https://files.quillbox.example/sh/59ryhdupqv2ncmx/MPT4c1ZLvWeQjHoNUyrA8BfxKs?dl=0
Should not have
• Nothing too busy.
• Not too many colors.
• Keep it simple, authentic, "down home."
• No homepage image sliders.

```html
<!DOCTYPE html>
<html lang="en">
<head>
<meta charset="utf-8">
<title>Kortie's Pit — Home</title>
<link rel="stylesheet" href="https://fonts.googleapis.com/css2?family=Roboto+Condensed:wght@400;700&family=Oswald:wght@300;700&family=Montserrat:wght@700&family=Lato:ital,wght@0,400;1,400&display=swap">
<style>
  :root {
    --brown: #4f1a04;
    --brown-text: #5a1d08;
    --orange: #f5a11c;
    --grey-text: #555;
    --story-text: #4a4a4a;
    --frame: #e3e3e3;
    --white: #fff;
  }
  * { margin: 0; padding: 0; box-sizing: border-box; }
  html, body { width: 1200px; height: 1200px; overflow: hidden; background: var(--white); }
  body { position: relative; font-family: "Lato", sans-serif; }

  .topbar { position: absolute; top: 0; left: 0; width: 1200px; height: 35px; background: var(--brown); }
  .topbar__welcome { position: absolute; left: 147px; top: 9px; font: 400 12px "Roboto Condensed", sans-serif; color: var(--white); }
  .topbar__welcome strong { color: var(--orange); font-weight: 700; }
  .social { position: absolute; right: 146px; top: 7px; display: flex; gap: 7px; }
  .social__item { width: 20px; height: 20px; border: 1px solid var(--orange); border-radius: 50%; }

  .nav { position: absolute; top: 35px; left: 0; width: 1200px; height: 77px; background: var(--white); }
  .nav__link { position: absolute; top: 33px; font: 700 12.5px "Roboto Condensed", sans-serif; color: var(--brown-text); letter-spacing: .2px; text-transform: uppercase; }
  .brand { position: absolute; left: 0; width: 1200px; top: 24px; text-align: center; font: 700 26px "Oswald", sans-serif; color: var(--orange); letter-spacing: 1px; text-transform: uppercase; }

  .hero { position: absolute; top: 112px; left: 0; width: 1200px; height: 509px;
    background:
      linear-gradient(180deg, rgba(14,40,60,0) 45%, rgba(14,40,60,.35) 100%),
      linear-gradient(180deg, #0f2a3c 0%, #16384c 30%, #3b2a22 52%, #7a3a1e 66%, #5a3526 80%, #2a3f55 100%); }
  .hero__panel { position: absolute; left: 255px; top: 139px; width: 691px; height: 250px;
    background: linear-gradient(180deg, rgba(5,8,10,.88) 0%, rgba(5,8,10,.82) 75%, rgba(5,8,10,0) 100%); }
  .hero__kicker { position: absolute; left: 0; width: 1200px; top: 160px; text-align: center; font: 300 46px "Oswald", sans-serif; color: var(--orange); line-height: 1; }
  .hero__title { position: absolute; left: 0; width: 1200px; top: 214px; text-align: center; font: 700 64px "Montserrat", sans-serif; color: var(--white); line-height: 1; }
  .hero__text { position: absolute; left: 0; width: 1200px; top: 294px; text-align: center; font: 400 14px/19px "Lato", sans-serif; color: var(--orange); }
  .hero__button { position: absolute; left: 530px; top: 366px; width: 140px; height: 46px; border: 2px solid var(--white); border-radius: 23px;
    background: rgba(0,0,0,.55); color: var(--orange); font: 700 10.5px/42px "Lato", sans-serif; text-align: center; text-transform: uppercase; }

  .about__title { position: absolute; left: 0; width: 1200px; top: 695px; text-align: center; font: 700 38px "Roboto Condensed", sans-serif; color: var(--orange); text-transform: uppercase; }
  .about__intro { position: absolute; left: 0; width: 1200px; top: 750px; text-align: center; font: 400 13px/20px "Lato", sans-serif; color: var(--grey-text); }

  .story__frame { position: absolute; left: 147px; top: 852px; width: 423px; height: 288px; background: var(--frame); padding: 7px; }
  .story__photo { width: 100%; height: 100%;
    background: linear-gradient(135deg, #b08a62 0%, #6a4a30 35%, #cfc6bb 55%, #3a2a22 80%, #8a5a4a 100%); }
  .story__title { position: absolute; left: 602px; top: 867px; font: 700 24px "Roboto Condensed", sans-serif; color: var(--brown); text-transform: uppercase; }
  .story__body { position: absolute; left: 602px; top: 915px; width: 445px; }
  .story__body p { font: italic 400 11.5px/18px "Lato", sans-serif; color: var(--story-text); margin-bottom: 14px; }
</style>
</head>
<body>
  <header>
    <div class="topbar">
      <p class="topbar__welcome">Welcome to <strong>KORTIE'S PIT</strong></p>
      <div class="social" aria-label="Social links">
        <span class="social__item"></span><span class="social__item"></span><span class="social__item"></span><span class="social__item"></span>
      </div>
    </div>
    <nav class="nav">
      <a class="nav__link" style="left:147px">Home</a>
      <a class="nav__link" style="left:210px">About</a>
      <a class="nav__link" style="left:275px">Locations</a>
      <a class="nav__link" style="left:362px">Restaurant Menus</a>
      <div class="brand">Kortie's Pit</div>
      <a class="nav__link" style="left:760px">Catering</a>
      <a class="nav__link" style="left:850px">News</a>
      <a class="nav__link" style="left:920px">Store</a>
      <a class="nav__link" style="left:994px">Contact Us</a>
    </nav>
  </header>

  <section class="hero" role="img" aria-label="Meat grilling on a barbecue grate under blue smoke">
    <div class="hero__panel"></div>
    <p class="hero__kicker">GOOD FOOD IS</p>
    <h1 class="hero__title">GOOD MOOD</h1>
    <p class="hero__text">Cras tincidunt elit mattis rhoncus faucibus. Mauris egestas mi elit. Donec pretium,<br>enim non sollicitudin congue, dolor turpis faucibus libero</p>
    <a class="hero__button">View All Store</a>
  </section>

  <section class="about">
    <h2 class="about__title">About Us</h2>
    <p class="about__intro">Cras tincidunt elit mattis rhoncus faucibus. Mauris egestas mi elit. Donec pretium,<br>enim non sollicitudin congue, dolor turpis faucibus libero,</p>
    <div class="story__frame">
      <div class="story__photo" role="img" aria-label="Plate of cornbread, collard greens and deviled eggs"></div>
    </div>
    <h3 class="story__title">Our Story</h3>
    <div class="story__body">
      <p>Lorem Ipsum is simply dummy text of the printing and typesetting industry. Lorem Ipsum has been the industry's stan when an unknown printer took a galley of type and scramble.</p>
      <p>Lorem Ipsum is simply dummy text of the printing and typesetting industry. Lorem Ipsum has been the industry's stan when an unknown printer took a galley of type and scramble.</p>
      <p>dard dummy text ever since the 1500s,when an unknown printer took a galley of type and scrambled it to make a type specimen book. It has survived not only five centurie.Lorem Ipsum is simply dummy text.</p>
      <p>Fusce suscipit malesuada ante, ac elementum ligula lobortis eget. Quisque interdum nec tellus et venenatis. Donec finibus blandit quam nec luctus.</p>
    </div>
  </section>
</body>
</html>
```